Stonebridge Building and Projects business cards

A business card with watermark background (construction work)

Company logo attached

Home improvement projects
House renovations
Bathroom and kitchen renovations
House extensions
New builds and granny flats

Director Omar Haddani
(Phone number)
omar@sbpbuilding.com.au
(Instagram logo) sbp_building

```html
<!DOCTYPE html>
<html lang="en">
<head>
<meta charset="utf-8">
<title>Stonebridge Building and Projects – Business Cards</title>
<link rel="stylesheet" href="https://fonts.googleapis.com/css2?family=Montserrat:wght@500;600;700&family=Roboto:wght@400;500&display=swap">
<style>
  :root {
    --page-bg: #e9eaec;
    --card-black: #111214;
    --card-black-soft: #1c1d20;
    --brand-blue: #0f7fd0;
    --brand-blue-dark: #0a62a6;
    --steel-grey: #8b8d92;
    --steel-light: #c9cbcf;
    --ink-white: #ffffff;
  }
  * { box-sizing: border-box; margin: 0; padding: 0; }
  html, body { width: 1200px; height: 1050px; overflow: hidden; }
  body {
    background: var(--page-bg);
    font-family: "Roboto", Arial, sans-serif;
    position: relative;
  }
  .card {
    position: absolute;
    left: 200px;
    width: 800px;
    height: 457px;
    border-radius: 26px;
    overflow: hidden;
    background: linear-gradient(135deg, var(--card-black-soft), var(--card-black));
    box-shadow: 0 10px 30px rgba(0,0,0,.25);
  }
  .card--front { top: 50px; }
  .card--back { top: 543px; }
  .card__art { position: absolute; inset: 0; width: 100%; height: 100%; }

  /* Front */
  .brand {
    position: absolute;
    left: 60px;
    top: 150px;
    color: var(--ink-white);
    font-family: "Montserrat", Arial, sans-serif;
    font-weight: 600;
    font-size: 26px;
    line-height: 1.2;
  }
  .brand__mark {
    display: inline-block;
    width: 14px; height: 14px;
    background: var(--brand-blue);
    margin-right: 10px;
  }
  .tagline {
    position: absolute;
    left: 60px;
    top: 240px;
    color: var(--brand-blue);
    font-family: "Montserrat", Arial, sans-serif;
    font-weight: 500;
    font-size: 21px;
    padding: 4px 0;
    border-top: 2px solid var(--brand-blue);
    border-bottom: 2px solid var(--brand-blue);
  }
  .person {
    position: absolute;
    right: 50px;
    top: 36px;
    text-align: right;
  }
  .person__name {
    color: var(--brand-blue);
    font-family: "Montserrat", Arial, sans-serif;
    font-weight: 700;
    font-size: 24px;
  }
  .person__role { color: var(--ink-white); font-size: 16px; margin-top: 2px; }
  .contact {
    position: absolute;
    right: 36px;
    top: 178px;
    list-style: none;
    color: var(--ink-white);
    font-size: 17px;
  }
  .contact__item {
    display: flex;
    justify-content: flex-end;
    align-items: center;
    gap: 14px;
    height: 28px;
  }
  .contact__icon { width: 16px; height: 16px; flex: none; }

  /* Back */
  .back-brand {
    position: absolute;
    left: 0; right: 0;
    top: 110px;
    text-align: center;
    color: var(--steel-grey);
    font-family: "Montserrat", Arial, sans-serif;
    font-weight: 600;
    font-size: 58px;
    letter-spacing: 1px;
  }
  .services {
    position: absolute;
    left: 0; right: 0;
    top: 262px;
    height: 86px;
    background: var(--brand-blue);
    color: var(--ink-white);
    font-size: 20px;
    line-height: 1.4;
    display: flex;
    flex-direction: column;
    justify-content: center;
    align-items: center;
  }
  .services__sep { margin: 0 8px; }
  .socials {
    position: absolute;
    left: 0; right: 0;
    top: 372px;
    display: flex;
    justify-content: center;
    gap: 40px;
    color: var(--steel-light);
    font-size: 18px;
  }
  .socials__item { display: flex; align-items: center; gap: 10px; }
  .socials__dot {
    width: 14px; height: 14px;
    border-radius: 50%;
    border: 2px solid var(--brand-blue);
  }
</style>
</head>
<body>

<section class="card card--front" aria-label="Business card front">
  <svg class="card__art" viewBox="0 0 800 457" aria-hidden="true">
    <path d="M0 450 C 240 462, 350 410, 440 290 C 510 185, 600 140, 800 130 L800 457 L0 457 Z" fill="var(--brand-blue)"/>
    <path d="M-10 412 C 230 428, 340 372, 428 252 C 500 150, 600 105, 810 95" fill="none" stroke="var(--steel-grey)" stroke-width="9"/>
  </svg>

  <div class="brand">
    <div><span class="brand__mark"></span>Stonebridge</div>
    <div>Building and Projects</div>
  </div>
  <div class="tagline">Built on solid ground!</div>

  <div class="person">
    <div class="person__name">Omar Haddani</div>
    <div class="person__role">Managing Director</div>
  </div>

  <ul class="contact">
    <li class="contact__item">0400 318 562
      <svg class="contact__icon" viewBox="0 0 16 16"><path d="M4 1.5 L6.5 4.5 L5 6.5 C6 8.5 7.5 10 9.5 11 L11.5 9.5 L14.5 12 L12.5 14.5 C7 14 2 9 1.5 3.5 Z" fill="none" stroke="#fff" stroke-width="1.4" stroke-linejoin="round"/></svg>
    </li>
    <li class="contact__item">sbp_building
      <svg class="contact__icon" viewBox="0 0 16 16"><circle cx="8" cy="8" r="6.5" fill="none" stroke="#fff" stroke-width="1.5"/></svg>
    </li>
    <li class="contact__item">omar@sbpbuilding.com.au
      <svg class="contact__icon" viewBox="0 0 16 16"><rect x="1" y="3" width="14" height="10" rx="1" fill="none" stroke="#fff" stroke-width="1.4"/><path d="M1.5 3.5 L8 9 L14.5 3.5" fill="none" stroke="#fff" stroke-width="1.4"/></svg>
    </li>
    <li class="contact__item">www.sbpbuilding.com.au
      <svg class="contact__icon" viewBox="0 0 16 16"><circle cx="8" cy="8" r="7" fill="#fff"/></svg>
    </li>
  </ul>
</section>

<section class="card card--back" aria-label="Business card back">
  <div class="back-brand">Stonebridge</div>

  <div class="services">
    <p>Home Improvement Projects<span class="services__sep">|</span>House Renovations<span class="services__sep">|</span>House Extensions</p>
    <p>Bathroom &amp; Kitchen Renovations<span class="services__sep">|</span>New Builds &amp; Granny Flats</p>
  </div>

  <div class="socials">
    <span class="socials__item"><span class="socials__dot"></span>sbp_building</span>
    <span class="socials__item"><span class="socials__dot"></span>sbpbuilding.com.au</span>
  </div>
</section>

</body>
</html>
```